Quorva - corporate Business Card

We need a good look and innovative business card for a new start up company based in Los Angeles called "Quorva". We are in a payment business, including payment card, app, and ewallet. We are expert in online payment and Card not present (CNP) transaction.
We need an innovative, modern business card.

Our logo font is Aero Matics

Target Market(s)

Startup - Bank - Online Payment - Card Manufacturing

Industry/Entity Type

Startup

Contact Information for Business Card

phone: 555 014 7396 - Address: 4172 Marlowe blvd, Cylver City, CA 90299

Requirements
Must have
• Message: innovative, professional, expert, high tech, trust, online payment expert, security
Nice to have
• no comment
Should not have
• no Comment

```html
<!DOCTYPE html>
<html lang="en">
<head>
<meta charset="utf-8">
<title>Quorva – Business Card</title>
<link href="https://fonts.googleapis.com/css2?family=Arimo:wght@400;700&display=swap" rel="stylesheet">
<style>
  :root {
    --stage: #2b2b2d;
    --paper: #f7f7f7;
    --brand-red: #c0222f;
    --brand-red-deep: #8e1620;
    --brand-pink: #d9737d;
    --ink-grey: #555a5e;
    --logo-grey: #e6e6e6;
  }
  * { margin: 0; padding: 0; box-sizing: border-box; }
  html, body { width: 1200px; height: 997px; overflow: hidden; }
  body {
    background: var(--stage);
    font-family: "Arimo", Arial, sans-serif;
    position: relative;
  }
  .card {
    position: absolute;
    width: 620px;
    height: 354px;
    left: 290px;
    border-radius: 2px;
    overflow: hidden;
    box-shadow: 0 10px 30px rgba(0,0,0,0.45);
  }
  /* Front: contact side */
  .card-front { top: 90px; background: var(--paper); }
  .front-disc {
    position: absolute;
    width: 300px; height: 300px;
    right: -40px; top: -90px;
    border-radius: 50%;
    background: var(--brand-pink);
  }
  .front-wordmark {
    position: absolute;
    left: 40px; top: 118px;
    font-size: 58px; font-weight: 700;
    color: var(--brand-red);
    letter-spacing: 1px;
  }
  .contact { position: absolute; left: 44px; top: 200px; }
  .contact-name {
    font-size: 15px; font-weight: 700; letter-spacing: 0.5px;
    color: var(--brand-red); text-transform: uppercase;
  }
  .contact-title { font-size: 14px; color: var(--ink-grey); margin-bottom: 16px; }
  .contact-address { font-size: 14px; font-weight: 700; color: var(--brand-red); line-height: 1.25; margin-bottom: 12px; }
  .contact-line { display: flex; align-items: center; gap: 10px; font-size: 14px; color: var(--ink-grey); margin-bottom: 6px; }
  .contact-icon { width: 18px; height: 18px; flex: none; }

  /* Back: brand side */
  .card-back {
    top: 510px;
    background: linear-gradient(135deg, var(--brand-red) 0%, #a81c27 55%, var(--brand-red-deep) 100%);
  }
  .back-disc {
    position: absolute;
    width: 160px; height: 160px;
    left: 230px; top: 52px;
    border-radius: 50%;
    background: #ffffff;
  }
  .back-wordmark {
    position: absolute;
    left: 0; right: 0; top: 226px;
    text-align: center;
    font-size: 66px; font-weight: 700;
    color: var(--logo-grey);
    letter-spacing: 2px;
  }
</style>
</head>
<body>
  <section class="card card-front" aria-label="Business card front">
    <div class="front-disc"></div>
    <div class="front-wordmark">quorva</div>
    <div class="contact">
      <p class="contact-name">Marisol Vantrel</p>
      <p class="contact-title">Attorney at Law</p>
      <p class="contact-address">4172 Marlowe blvd,<br>Cylver City, CA 90299</p>
      <p class="contact-line">
        <svg class="contact-icon" viewBox="0 0 18 18" aria-hidden="true">
          <circle cx="9" cy="9" r="9" fill="#c0222f"/>
          <path d="M5.5 6.5c0-.8.6-1.3 1.2-1.3h4.6c.6 0 1.2.5 1.2 1.3L11 8H7z M6 9.5h6l.6 3.3H5.4z" fill="#fff"/>
        </svg>
        555 014 7396
      </p>
      <p class="contact-line">
        <svg class="contact-icon" viewBox="0 0 18 18" aria-hidden="true">
          <circle cx="9" cy="9" r="9" fill="#c0222f"/>
          <rect x="4.5" y="6" width="9" height="6.5" rx="0.8" fill="#fff"/>
          <path d="M4.8 6.3 9 9.6l4.2-3.3" fill="none" stroke="#c0222f" stroke-width="1"/>
        </svg>
        marisol@quorva.com
      </p>
    </div>
  </section>

  <section class="card card-back" aria-label="Business card back">
    <div class="back-disc"></div>
    <div class="back-wordmark">quorva</div>
  </section>
</body>
</html>
```